Business Card Design for Training Business

Clear Path Coaching is a new business that delivers training and other services with a focus on topics related to mental health and wellbeing, for example, Wellmind Response Course, Resilience etc. We have a strong focus on evidence-based psychology and neuroscience. I have a logo which I will upload with the brief, so please consider colours that work well with the logo.
Target Market(s)
Adults, workplaces (particularly government and not-for-profits)
Industry/Entity Type
Business
Contact Information for Business Card
Head Strong TrainingSamantha SellwoodDirector0438 770 850sam@headstrongtraining.com.auwww.headstrongtraining.com.au

```html
<!DOCTYPE html>
<html lang="en">
<head>
<meta charset="utf-8">
<title>Clear Path Coaching – Business Card</title>
<link href="https://fonts.googleapis.com/css2?family=Questrial&display=swap" rel="stylesheet">
<style>
  :root {
    --backdrop: #2f2f2f;
    --teal: #22b8bc;
    --teal-deep: #1aa9ae;
    --mint: #bfe6dc;
    --paper: #f6f6f6;
    --white: #ffffff;
    --ink-grey: #7a7a7a;
  }
  * { margin: 0; padding: 0; box-sizing: border-box; }
  html, body { width: 1200px; height: 750px; overflow: hidden; }
  body {
    background: var(--backdrop);
    font-family: "Questrial", "Century Gothic", sans-serif;
    position: relative;
  }
  .card {
    position: absolute;
    top: 228px;
    width: 461px;
    height: 262px;
    overflow: hidden;
  }
  .card-front { left: 124px; background: var(--teal); color: var(--white); }
  .card-back { left: 590px; background: var(--paper); }

  .pattern-area {
    position: absolute;
    width: 264px;
    height: 264px;
    top: -1px;
    border-radius: 50%;
    background: radial-gradient(circle, var(--white) 0%, var(--mint) 55%, var(--teal) 100%);
  }
  .card-front .pattern-area {
    left: 329px;
    box-shadow: 0 0 0 4px var(--white);
  }
  .card-back .pattern-area { left: -136px; }

  .brand-name {
    position: absolute;
    left: 40px;
    top: 48px;
    width: 210px;
    text-align: center;
    font-weight: 400;
    letter-spacing: 0.12em;
    text-transform: uppercase;
    line-height: 1;
  }
  .brand-name .line-main { display: block; font-size: 22px; }
  .brand-name .line-sub { display: block; font-size: 11px; letter-spacing: 0.42em; margin-top: 8px; }

  .person { position: absolute; left: 41px; top: 116px; }
  .person-name { font-size: 18px; font-weight: 400; }
  .person-role { font-size: 13px; margin-top: 1px; }

  .contacts { position: absolute; left: 42px; top: 166px; list-style: none; font-size: 12px; }
  .contacts li { display: flex; align-items: center; height: 18px; }
  .contacts svg { width: 12px; height: 12px; margin-right: 7px; fill: var(--white); }

  .back-logo {
    position: absolute;
    left: 0; right: 0;
    top: 80px;
    display: flex;
    flex-direction: column;
    align-items: center;
    color: var(--ink-grey);
  }
  .back-logo .mark {
    width: 60px; height: 60px;
    border-radius: 50%;
    background: var(--teal);
    opacity: 0.55;
    margin-left: -4px;
  }
  .back-logo .brand-name {
    position: static;
    width: auto;
    margin-top: 14px;
  }
  .back-logo .line-main { font-size: 19px; }
  .back-logo .line-sub { font-size: 9.5px; margin-top: 6px; }
</style>
</head>
<body>
  <section class="card card-front">
    <div class="pattern-area" role="img" aria-label="Decorative geometric rosette pattern in teal and mint"></div>
    <h1 class="brand-name"><span class="line-main">Clear Path</span><span class="line-sub">Coaching</span></h1>
    <div class="person">
      <p class="person-name">Rebecca Tanfield</p>
      <p class="person-role">Director</p>
    </div>
    <ul class="contacts">
      <li><svg viewBox="0 0 24 24" aria-hidden="true"><path d="M6.6 10.8a15.1 15.1 0 0 0 6.6 6.6l2.2-2.2c.3-.3.7-.4 1-.2 1.1.4 2.3.6 3.6.6.6 0 1 .4 1 1V20c0 .6-.4 1-1 1A17 17 0 0 1 3 4c0-.6.4-1 1-1h3.5c.6 0 1 .4 1 1 0 1.3.2 2.5.6 3.6.1.3 0 .7-.2 1l-2.3 2.2z"/></svg>0491 362 517</li>
      <li><svg viewBox="0 0 24 24" aria-hidden="true"><path d="M2 5h20v14H2z M2 5l10 8 10-8" /></svg>bec@clearpathcoaching.example.au</li>
      <li><svg viewBox="0 0 24 24" aria-hidden="true"><circle cx="12" cy="12" r="10"/></svg>www.clearpathcoaching.example.au</li>
    </ul>
  </section>

  <section class="card card-back">
    <div class="pattern-area" role="img" aria-label="Decorative geometric rosette pattern in teal and mint"></div>
    <div class="back-logo">
      <span class="mark" aria-hidden="true"></span>
      <p class="brand-name"><span class="line-main">Clear Path</span><span class="line-sub">Coaching</span></p>
    </div>
  </section>
</body>
</html>
```